Food broker, trader, wholesaler, liquidator looking for a 5 pages website

Looking for a 5 pages website design. We are food brokers, traders, wholesaler and closeout buyer working with manufacturers, distributors, importers sell to retailers, food service operators and industrial (ingredients). We help market their products. We are a resource for those who need a solution in the distribution/selling/placement of food on the shelves, kitchens and pantries. Whether we open new accounts with new products or sell short dated inventory, we know where to go and get results.

Target Market(s)

Food manufacturers, food distributors, food brokers

Coding

Coded - Design and coding required

Number of Pages Required

4 page

Font styles to use
Serif

Requirements
Must have
• Food-food production-warehouse-Food packaging-people meeting-trucks-supermarket shelves-

```html
<!DOCTYPE html>
<html lang="en">
<head>
<meta charset="utf-8">
<title>Harborline Provisions</title>
<link rel="stylesheet" href="https://fonts.googleapis.com/css2?family=Noto+Serif:wght@400;700&family=Merriweather+Sans:wght@300;400&family=Tinos&family=Exo:wght@400;500&display=swap">
<style>
:root{
  --navy:#0d0b4f;
  --topbar:#6d6d6d;
  --header:#f8f8f8;
  --lavender:#e2e2f5;
  --cycle:#2e3244;
  --footer:#222228;
  --ink:#222;
  --white:#fff;
}
*{box-sizing:border-box;margin:0;padding:0}
html,body{width:1200px;height:3602px;overflow:hidden}
body{font-family:"Merriweather Sans",sans-serif;color:var(--ink);background:#fff;position:relative}
.serif{font-family:"Noto Serif",serif}
section,header,footer,.topbar{position:absolute;left:0;width:1200px}
.abs{position:absolute}

.topbar{top:0;height:49px;background:var(--topbar);color:#fff;font-family:"Noto Serif",serif}
.topbar .phone{left:86px;top:14px;font-size:17px;font-weight:700;display:flex;align-items:center;gap:12px}
.topbar .login{left:936px;top:16px;font-size:13px;font-weight:700}
.topbar .sep{left:1011px;top:13px;font-size:15px}
.topbar .register{left:1036px;top:9px;width:90px;height:31px;background:var(--navy);border-radius:6px;font-size:13px;font-weight:700;display:flex;align-items:center;justify-content:center}

.site-header{top:49px;height:116px;background:var(--header)}
.brand{left:63px;top:10px;width:214px;height:100px;background:#fff;display:flex;flex-direction:column;align-items:center;justify-content:center;gap:8px}
.brand .mark{width:90px;height:60px;border-radius:50%;background:var(--navy)}
.brand .name{font-family:"Noto Serif",serif;font-weight:700;font-size:12px;color:var(--navy)}
.nav{right:74px;top:44px;display:flex;gap:40px;font-family:"Noto Serif",serif;font-size:16px;color:#333;align-items:center}
.nav .active{background:var(--navy);color:#fff;padding:6px 13px;border-radius:6px;margin-right:-11px}

.hero{top:165px;height:593px;background:linear-gradient(100deg,#6e6fa6 0%,#5b6e94 40%,#4e7a6a 70%,#5d7e5a 100%)}
.hero h1{left:102px;top:180px;font-family:"Noto Serif",serif;font-size:40px;font-weight:700;color:#fff}
.hero p{left:105px;top:242px;width:430px;font-size:16.5px;line-height:28px;color:#fff;font-weight:300}
.hero .cta{left:105px;top:353px;width:182px;height:50px;border-radius:25px;background:var(--navy);color:#fff;font-family:"Noto Serif",serif;font-weight:700;font-size:18px;display:flex;align-items:center;justify-content:center}
.hero .dots{left:577px;top:498px;display:flex;gap:13px}
.hero .dots i{width:6px;height:6px;border-radius:50%;background:#fff;display:block}

.welcome{top:758px;height:263px;text-align:center}
.welcome .kicker{margin-top:46px;font-family:"Noto Serif",serif;font-size:14px;color:#333}
.welcome h2{margin-top:12px;font-family:"Noto Serif",serif;font-size:25px;font-weight:700;color:var(--navy)}
.welcome p{margin:16px auto 0;width:770px;font-size:13.5px;line-height:22.5px;color:#222}

.what{top:1021px;height:594px;background:var(--lavender)}
.what h2{position:absolute;top:48px;width:100%;text-align:center;font-family:"Noto Serif",serif;font-size:25px;font-weight:700;color:var(--navy)}
.card{position:absolute;top:126px;width:250px;height:379px;background:#fff;text-align:center;color:#111}
.card.featured{background:var(--navy);color:#fff}
.card svg.icon{margin-top:10px}
.card h3{font-family:"Noto Serif",serif;font-weight:700;font-size:23px;line-height:29px;margin-top:16px}
.card p{font-size:11.5px;line-height:22px;margin:18px auto 0;width:200px}
.card .go{position:absolute;left:105px;top:313px;width:40px;height:40px;border-radius:50%;background:var(--navy);display:flex;align-items:center;justify-content:center}
.card.featured .go{background:#fff}

.pride{top:1615px;height:434px;text-align:center}
.pride .art{left:462px;top:42px;width:272px;height:178px;border-radius:14px;background:radial-gradient(circle at 50% 55%,#d98a4e 0%,#f3dcc6 45%,#fff 75%)}
.pride p{position:absolute;top:264px;width:100%;font-family:"Exo",sans-serif;font-size:19px;line-height:28px;color:#111}

.cycle{top:2049px;height:1401px;background:var(--cycle);color:#fff}
.cycle h2{position:absolute;top:50px;width:100%;text-align:center;font-family:"Noto Serif",serif;font-size:25px;font-weight:700}
.cycle .spine{left:599px;top:105px;width:2px;height:1089px;background:#d9d9d9}
.cycle .spine-dot{left:595px;top:100px;width:10px;height:10px;border-radius:50%;background:#fff}
.tick{position:absolute;height:2px;width:34px;background:#d9d9d9}
.stage{position:absolute;width:330px;font-family:"Tinos",serif}
.stage h3{font-weight:400;font-size:26px;letter-spacing:.3px}
.stage p{font-size:12.5px;line-height:22px;margin-top:4px}
.stage.left{left:173px;text-align:right}
.stage.right{left:694px;text-align:left}
.disc{position:absolute;border-radius:50%}

.help{left:990px;top:3425px;width:136px;height:50px;border-radius:25px;background:var(--navy);color:#fff;font-weight:700;font-size:19px;display:flex;align-items:center;justify-content:center;gap:12px;z-index:2}

.site-footer{top:3450px;height:152px;background:var(--footer);color:#fff;font-family:"Noto Serif",serif}
.site-footer .mark{left:150px;top:12px;width:114px;height:82px;border-radius:50%;background:var(--navy)}
.site-footer .name{left:111px;top:114px;font-weight:700;font-size:15px}
.site-footer .fnav{left:536px;top:56px;display:flex;gap:40px;font-size:16px}
.site-footer .copy{right:73px;top:98px;font-size:14px;display:flex;align-items:center;gap:8px}
</style>
</head>
<body>

<div class="topbar">
  <div class="abs phone">
    <svg width="14" height="14" viewBox="0 0 24 24"><path fill="#fff" d="M6.6 10.8a15.1 15.1 0 0 0 6.6 6.6l2.2-2.2c.3-.3.7-.4 1-.2 1.1.4 2.3.6 3.6.6.6 0 1 .4 1 1V20c0 .6-.4 1-1 1A17 17 0 0 1 3 4c0-.6.4-1 1-1h3.5c.6 0 1 .4 1 1 0 1.3.2 2.5.6 3.6.1.3 0 .7-.2 1z"/></svg>
    1-800 555 0142
  </div>
  <div class="abs login">LOGIN</div>
  <div class="abs sep">|</div>
  <div class="abs register">REGISTER</div>
</div>

<header class="site-header">
  <div class="abs brand">
    <span class="mark"></span>
    <span class="name">HARBORLINE PROVISIONS</span>
  </div>
  <nav class="abs nav">
    <span class="active">HOME</span><span>ABOUT US</span><span>WHAT WE DO</span><span>CONTACT</span><span>GIVING BACK</span>
  </nav>
</header>

<section class="hero" role="img" aria-label="Smiling grocer holding a box of green peppers in a greenhouse">
  <h1 class="abs">HARBORLINE PROVISIONS</h1>
  <p class="abs">Harborline Provisions works with food manufacturers, brand owners, distributors and wholesalers market their products.</p>
  <div class="abs cta">Get in touch</div>
  <div class="abs dots"><i></i><i></i><i></i></div>
</section>

<section class="welcome">
  <div class="kicker">WELCOME</div>
  <h2>HARBORLINE PROVISIONS</h2>
  <p>Retail, Food Service and Industrial ingredients.<br>Founded in 2008, Harborline Provisions started with the distribution of gluten free products understanding the need to provide access to unique flavors and products for the celiac consumers. From this, we expanded into deli, dairy, groceries, frozen and beverages.</p>
</section>

<section class="what">
  <h2>WHAT WE DO</h2>
  <div class="card" style="left:207px">
    <svg class="icon" width="120" height="110" viewBox="0 0 120 110" fill="none" stroke="#111" stroke-width="3.5" stroke-linejoin="round">
      <path d="M20 45h22l34-22v64L42 65H20z"/><path d="M28 65l6 24h10l-4-24"/><path d="M76 30c6 4 6 46 0 50"/>
      <path d="M88 40v26M100 24l-8 8M100 82l-8-8M104 53h-8M95 12l-5 7M95 96l-5-7"/>
    </svg>
    <h3>SALES &amp;<br>MARKETING</h3>
    <p>we connect food buyers and sellers through a dedicated approach.</p>
    <div class="go"><svg width="10" height="10" viewBox="0 0 10 10"><path d="M3 1l4 4-4 4" stroke="#fff" stroke-width="2" fill="none"/></svg></div>
  </div>
  <div class="card featured" style="left:475px">
    <svg class="icon" width="120" height="110" viewBox="0 0 120 110" fill="none" stroke="#fff" stroke-width="3.5" stroke-linejoin="round">
      <rect x="16" y="20" width="88" height="64"/><rect x="24" y="28" width="72" height="48"/><path d="M50 84v10M70 84v10M40 96h40"/>
      <path d="M30 36h8v6h-8zM30 48h8v6h-8zM30 60h8v6h-8zM44 39h12M44 51h12M44 63h12M62 60l8-10 6 6 10-16"/>
    </svg>
    <h3>TRADING</h3>
    <p>we purchase goods anywhere and ship them Nationwide and Export.</p>
    <div class="go"><svg width="10" height="10" viewBox="0 0 10 10"><path d="M3 1l4 4-4 4" stroke="#0d0b4f" stroke-width="2" fill="none"/></svg></div>
  </div>
  <div class="card" style="left:743px">
    <svg class="icon" width="120" height="110" viewBox="0 0 120 110" fill="none" stroke="#111" stroke-width="3.5" stroke-linejoin="round">
      <path d="M12 44L60 8l48 36"/><path d="M22 38v62h76V38"/><rect x="38" y="52" width="44" height="40"/><rect x="50" y="52" width="20" height="22"/><path d="M56 66l4-4 4 4"/>
    </svg>
    <h3>CLOSEOUT/<br>EXCESS<br>INVENTORY</h3>
    <p>we buy closeouts and excess inventory for prisons, outlet stores and discounters.</p>
    <div class="go"><svg width="10" height="10" viewBox="0 0 10 10"><path d="M3 1l4 4-4 4" stroke="#fff" stroke-width="2" fill="none"/></svg></div>
  </div>
</section>

<section class="pride">
  <div class="abs art" role="img" aria-label="Illustration of a shopper and a grocer sharing a box of groceries"></div>
  <p>We pride ourselves in working in an easy, personal and accessible environment<br>making our customers and vendors comfortable with us.<br>We look forward to connecting with you and evaluating how we can assist you<br>reaching your sales objectives.</p>
</section>

<section class="cycle">
  <h2>OUR CYCLE</h2>
  <div class="abs spine"></div>
  <div class="abs spine-dot"></div>

  <div class="tick" style="left:566px;top:158px"></div>
  <div class="tick" style="left:600px;top:315px"></div>
  <div class="tick" style="left:566px;top:477px"></div>
  <div class="tick" style="left:600px;top:636px"></div>
  <div class="tick" style="left:566px;top:809px"></div>
  <div class="tick" style="left:600px;top:969px"></div>
  <div class="tick" style="left:566px;top:1141px"></div>

  <div class="stage left" style="top:140px"><h3>FOOD</h3><p>Lorem ipsum dolor sit amet, consectetur<br>adipiscing elit, sed do eiusmod tempor<br>incididunt ut labore et dolore magna aliqua.<br>Ut enim ad minim veniam</p></div>
  <div class="stage right" style="top:302px"><h3>FOOD PRODUCTION</h3><p>Lorem ipsum dolor sit amet, consectetur<br>adipiscing elit, sed do eiusmod tempor<br>incididunt ut labore et dolore magna aliqua.<br>Ut enim ad minim veniam</p></div>
  <div class="stage left" style="top:464px"><h3>WAREHOUSE</h3><p>Lorem ipsum dolor sit amet, consectetur<br>adipiscing elit, sed do eiusmod tempor<br>incididunt ut labore et dolore magna aliqua.<br>Ut enim ad minim veniam</p></div>
  <div class="stage right" style="top:626px"><h3>FOOD PACKAGING</h3><p>Lorem ipsum dolor sit amet, consectetur<br>adipiscing elit, sed do eiusmod tempor<br>incididunt ut labore et dolore magna aliqua.<br>Ut enim ad minim veniam</p></div>
  <div class="stage left" style="top:790px"><h3>PEOPLE MEETING</h3><p>Lorem ipsum dolor sit amet, consectetur<br>adipiscing elit, sed do eiusmod tempor<br>incididunt ut labore et dolore magna aliqua.<br>Ut enim ad minim veniam</p></div>
  <div class="stage right" style="top:952px"><h3>TRUCKS</h3><p>Lorem ipsum dolor sit amet, consectetur<br>adipiscing elit, sed do eiusmod tempor<br>incididunt ut labore et dolore magna aliqua.<br>Ut enim ad minim veniam</p></div>
  <div class="stage left" style="top:1125px"><h3>SUPERMARKET SHELVES</h3><p>Lorem ipsum dolor sit amet, consectetur<br>adipiscing elit, sed do eiusmod tempor<br>incididunt ut labore et dolore magna aliqua.<br>Ut enim ad minim veniam</p></div>

  <div class="disc" role="img" aria-label="Illustration of a served food dish under a cloche" style="left:729px;top:121px;width:152px;height:152px;background:#27a9c9"></div>
  <div class="disc" role="img" aria-label="Illustration of yellow and red bell peppers" style="left:351px;top:290px;width:154px;height:154px;background:#3bb3a0"></div>
  <div class="disc" role="img" aria-label="Illustration of a warehouse building" style="left:711px;top:452px;width:154px;height:154px;background:#8fa9b6"></div>
  <div class="abs" role="img" aria-label="Illustration of a taped cardboard package" style="left:354px;top:630px;width:118px;height:136px;background:linear-gradient(135deg,#f3b25a,#e8893e);border-radius:8px"></div>
  <div class="disc" role="img" aria-label="Illustration of two business people meeting over coffee" style="left:694px;top:778px;width:154px;height:154px;background:linear-gradient(180deg,#3a9de0 65%,#f5b82e 65%)"></div>
  <div class="disc" role="img" aria-label="Illustration of a delivery truck" style="left:303px;top:941px;width:156px;height:156px;background:#8cc84b"></div>
  <div class="disc" role="img" aria-label="Illustration of a shopper at supermarket shelves with a basket" style="left:691px;top:1121px;width:160px;height:160px;background:linear-gradient(135deg,#2fbf86,#1c8f68)"></div>
</section>

<div class="abs help">Help
  <svg width="18" height="18" viewBox="0 0 20 20"><circle cx="10" cy="10" r="8" stroke="#fff" stroke-width="2" fill="none"/><path d="M7.5 8a2.5 2.5 0 1 1 3.5 2.3c-.7.3-1 .8-1 1.5" stroke="#fff" stroke-width="2" fill="none"/><circle cx="10" cy="14.6" r="1.1" fill="#fff"/></svg>
</div>

<footer class="site-footer">
  <span class="abs mark"></span>
  <span class="abs name">HARBORLINE PROVISIONS</span>
  <nav class="abs fnav"><span>HOME</span><span>ABOUT US</span><span>WHAT WE DO</span><span>CONTACT</span><span>GIVING BACK</span></nav>
  <div class="abs copy">
    <svg width="14" height="14" viewBox="0 0 20 20"><circle cx="10" cy="10" r="8" stroke="#fff" stroke-width="2" fill="none"/><path d="M12.5 7.5a3.5 3.5 0 1 0 0 5" stroke="#fff" stroke-width="2" fill="none"/></svg>
    <span>&nbsp;2020 &nbsp;|&nbsp; www.harborlineprovisions.com</span>
  </div>
</footer>

</body>
</html>
```